Coffee Bag Design for Tollbury Coffee

We’re excited to invite you to help us bring Tollbury Coffee to life on grocery store shelves with a design that embodies our mission of spreading goodness and creating a lasting impact. Tollbury Coffee represents warmth, positivity, and the power of small actions to create ripples of goodness. Each cup not only offers a rich, gourmet coffee experience but also gives back to the community, with $2 from each bag supporting local food banks.

To reflect this vision, we’d love for the design to feature a dark (greyish) blue as the base color to convey depth and quality, complemented by a vibrant light blue that will catch the eye and add energy. Tan or gold accents could add an elegant touch and a feeling of warmth. We are aiming for a look that feels uplifting and engaging, with simplicity and elegance, yet stands out amid other brands on the shelf.

I am attaching the dimension of the bag.

Other information that needs to be listed:
Ingredients: 100% Arabica Coffee
Net Wt. 12 oz. (340 g)
Roasted and distributed by:
Name
Address
email

Text on the back of the bag:
Tollbury Coffee is crafted with a belief that kindness and positivity can spread, touching countless lives with every sip. This gourmet blend delivers a rich taste experience while giving back, as $2 from each bag sold is donated to local food banks to help those in need. Enjoy the warmth and goodness in each cup, knowing you’re making a difference with every purchase.

Thank you!

```html
<!DOCTYPE html>
<html lang="en">
<head>
<meta charset="utf-8">
<title>Tollbury Coffee – Bag Dieline</title>
<link rel="stylesheet" href="https://fonts.googleapis.com/css2?family=Fira+Sans:wght@400;500;600;800&family=Fira+Sans+Condensed:wght@600&display=swap">
<style>
  :root{
    --stage:#6a6a6a;
    --navy:#3c5f7d;
    --navy-deep:#345571;
    --aqua:#8fd4d7;
    --aqua-soft:#b9e4e6;
    --gold:#b8853a;
    --gold-light:#e2bf6e;
    --white:#ffffff;
    --ink-light:#eef6f7;
    --guide:#c88fd0;
  }
  *{box-sizing:border-box;margin:0;padding:0}
  html,body{width:960px;height:1200px;overflow:hidden}
  body{
    background:radial-gradient(ellipse at 50% 45%,#8a8a8a 0%,var(--stage) 70%);
    font-family:"Fira Sans",sans-serif;color:var(--ink-light);
    position:relative;
  }
  .dieline{position:absolute;left:20px;top:340px;width:921px;height:520px}
  .panel{
    position:absolute;overflow:hidden;border-radius:10px;
    background:var(--navy);
    box-shadow:0 4px 10px rgba(0,0,0,.35);
  }
  .panel::after{
    content:"";position:absolute;inset:6px;border:1px dashed var(--guide);
    border-radius:6px;opacity:.7;pointer-events:none;
  }
  .panel--side-left{left:0;top:0;width:159px;height:360px}
  .panel--front{left:160px;top:0;width:300px;height:360px}
  .panel--side-right{left:461px;top:0;width:159px;height:360px}
  .panel--back{left:621px;top:0;width:300px;height:360px}
  .panel--bottom{left:160px;top:361px;width:300px;height:158px}

  .marble{
    position:absolute;
    background:
      radial-gradient(ellipse at 45% 35%,#f2fafb 0%,rgba(242,250,251,0) 45%),
      radial-gradient(ellipse at 80% 80%,#5aaabb 0%,rgba(90,170,187,0) 55%),
      linear-gradient(160deg,#7cc6d0 0%,#cdeaee 40%,#9ed6dc 65%,#4f9fb2 100%);
  }
  .panel--front .marble{left:119px;top:0;right:0;bottom:0}
  .panel--back .marble{inset:0}

  .front-band{position:absolute;left:0;top:0;width:113px;height:100%;background:var(--navy)}
  .gold-rule{
    position:absolute;left:113px;top:0;width:6px;height:100%;
    background:linear-gradient(180deg,var(--gold) 0%,var(--gold-light) 50%,var(--gold) 100%);
  }
  .brand-vertical{
    position:absolute;writing-mode:vertical-rl;
    font-family:"Fira Sans",sans-serif;font-weight:800;letter-spacing:1px;
    white-space:nowrap;line-height:1;
  }
  .panel--front .brand-vertical{left:34px;top:48px;font-size:34px;color:var(--aqua)}
  .panel--side-left .brand-vertical{left:60px;top:70px;font-size:27px;color:var(--white)}

  .info-card{
    position:absolute;left:128px;top:132px;width:153px;height:132px;
    background:var(--navy);text-align:center;padding-top:10px;
  }
  .info-card__title{font-weight:600;font-size:10px;letter-spacing:1.4px}
  .info-card__value{font-size:9px;letter-spacing:.8px;margin-top:3px}
  .info-card__rule{border-top:1px dashed var(--ink-light);margin:7px 8px}
  .roast-scale{display:flex;justify-content:center;gap:7px;margin-top:5px}
  .roast-scale svg{width:15px;height:13px}

  .side-logo{
    position:absolute;top:140px;left:0;width:100%;text-align:center;
    font-weight:800;font-size:17px;color:var(--white);letter-spacing:.5px;
  }
  .side-block{position:absolute;left:0;width:100%;font-size:9px;letter-spacing:.8px;line-height:15px}
  .side-block--ingredients{top:180px;text-align:center}
  .side-block--distributor{top:236px;padding-left:20px}
  .side-label{font-weight:600}
  .roasted-band{
    position:absolute;left:0;top:289px;width:100%;height:36px;background:var(--aqua);
    color:var(--navy);text-align:center;font-family:"Fira Sans Condensed",sans-serif;
    font-weight:600;font-size:11px;line-height:15px;padding-top:3px;
  }

  .zip-guide{position:absolute;left:16px;right:0;top:48px;height:42px;background:rgba(200,140,210,.35)}
  .zip-guide::before{content:"";position:absolute;left:0;right:0;top:10px;height:2px;background:rgba(170,80,180,.7)}
  .squeeze-mark{position:absolute;left:112px;top:126px;width:76px;height:70px}
  .mission{
    position:absolute;left:25px;top:191px;width:248px;height:118px;
    background:var(--navy-deep);border:2px solid var(--gold);border-radius:9px;
    padding:8px 10px;font-size:7.6px;line-height:14.4px;text-align:justify;text-align-last:center;
    color:var(--white);
  }
  .net-weight{
    position:absolute;left:0;width:100%;top:318px;text-align:center;
    font-family:"Fira Sans Condensed",sans-serif;font-weight:600;font-size:9px;color:var(--white);
  }
</style>
</head>
<body>
<main class="dieline" aria-label="Tollbury Coffee bag dieline">

  <section class="panel panel--side-left">
    <span class="brand-vertical">TOLLBURY COFFEE</span>
  </section>

  <section class="panel panel--front">
    <div class="front-band"></div>
    <div class="gold-rule"></div>
    <div class="marble" role="img" aria-label="Aqua and white fluid ink texture with gold veins"></div>
    <span class="brand-vertical">TOLLBURY COFFEE</span>
    <div class="info-card">
      <p class="info-card__title">Type Of Coffee</p>
      <p class="info-card__value">Colombian, Morning Blend</p>
      <div class="info-card__rule"></div>
      <p class="info-card__title">Roast</p>
      <div class="roast-scale" aria-label="Roast level scale">
        <svg viewBox="0 0 15 13"><ellipse cx="7.5" cy="6.5" rx="6.5" ry="5.5" fill="#dcb593" stroke="#fff" stroke-width="1"/><path d="M3 8 Q7.5 4 12 5" stroke="#fff" fill="none"/></svg>
        <svg viewBox="0 0 15 13"><ellipse cx="7.5" cy="6.5" rx="6.5" ry="5.5" fill="#c48c5f" stroke="#fff" stroke-width="1"/><path d="M3 8 Q7.5 4 12 5" stroke="#fff" fill="none"/></svg>
        <svg viewBox="0 0 15 13"><ellipse cx="7.5" cy="6.5" rx="6.5" ry="5.5" fill="#9a5a3a" stroke="#fff" stroke-width="1"/><path d="M3 8 Q7.5 4 12 5" stroke="#fff" fill="none"/></svg>
        <svg viewBox="0 0 15 13"><ellipse cx="7.5" cy="6.5" rx="6.5" ry="5.5" fill="#7a3324" stroke="#fff" stroke-width="1"/><path d="M3 8 Q7.5 4 12 5" stroke="#fff" fill="none"/></svg>
        <svg viewBox="0 0 15 13"><ellipse cx="7.5" cy="6.5" rx="6.5" ry="5.5" fill="#4a1e22" stroke="#fff" stroke-width="1"/><path d="M3 8 Q7.5 4 12 5" stroke="#fff" fill="none"/></svg>
      </div>
      <div class="info-card__rule"></div>
      <p class="info-card__title">Flavor</p>
    </div>
  </section>

  <section class="panel panel--side-right">
    <p class="side-logo">TOLLBURY COFFEE</p>
    <div class="side-block side-block--ingredients">
      <p class="side-label">Ingredients:</p>
      <p>100% Arabica</p>
      <p>Coffee-Roasted</p>
    </div>
    <div class="side-block side-block--distributor">
      <p class="side-label">Distributed by:</p>
      <p>Name :</p>
      <p>Address :</p>
    </div>
    <div class="roasted-band">Proudly<br>Roasted in Pittsburgh</div>
  </section>

  <section class="panel panel--back">
    <div class="marble" role="img" aria-label="Aqua and white fluid ink texture with gold veins"></div>
    <div class="zip-guide"></div>
    <svg class="squeeze-mark" viewBox="0 0 76 70" aria-label="Squeeze Me To Smell">
      <defs><path id="squeeze-arc" d="M10 52 A28 28 0 0 1 66 52"/></defs>
      <circle cx="38" cy="46" r="21" fill="none" stroke="#1f3f8a" stroke-width="1"/>
      <text font-family="Fira Sans, sans-serif" font-weight="600" font-size="7.5" fill="#1b1b1b">
        <textPath href="#squeeze-arc" startOffset="50%" text-anchor="middle">Squeeze Me To Smell</textPath>
      </text>
    </svg>
    <p class="mission">Tollbury Coffee is crafted with the belief that kindness and positivity can spread, touching countless lives with every sip. This gourmet blend delivers a rich taste experience while giving back, as $2 from each bag sold is donated to local food banks to help those in need. Enjoy the warmth and goodness in each cup, knowing you’re making a difference with every purchase.</p>
    <p class="net-weight">Net Wt. 12 oz. (340 g)</p>
  </section>

  <section class="panel panel--bottom"></section>

</main>
</body>
</html>
```